Veldmark Supplies Business Card

Professional business card that stand out to our potential customers. Front and back with clean modern design

Industry/Entity Type

Oil and gas

Contact Information for Business Card

Name, address, website , office phone and cell number

Requirements
Must have
• Editable files for each employee

```html
<!DOCTYPE html>
<html lang="en">
<head>
<meta charset="utf-8">
<title>Veldmark Supplies – Business Card</title>
<link rel="stylesheet" href="https://fonts.googleapis.com/css2?family=Open+Sans:wght@400;600;700&display=swap">
<style>
  :root {
    --bg-outer: #0d0d0d;
    --bg-inner: #2a2a2a;
    --card: #222223;
    --red: #ff0a0a;
    --cyan: #05b0d0;
    --text-light: #e8e8e8;
    --card-w: 540px;
    --card-h: 309px;
  }
  * { box-sizing: border-box; margin: 0; padding: 0; }
  html, body { width: 1200px; height: 801px; overflow: hidden; }
  body {
    background: radial-gradient(ellipse at 60% 45%, var(--bg-inner) 0%, #1b1b1b 45%, var(--bg-outer) 100%);
    font-family: "Open Sans", Arial, sans-serif;
    position: relative;
  }
  .card {
    position: absolute;
    top: 246px;
    width: var(--card-w);
    height: var(--card-h);
    background: var(--card);
    border-radius: 14px;
    overflow: hidden;
    box-shadow: 0 18px 40px rgba(0,0,0,0.55);
  }
  .card--front { left: 40px; }
  .card--back { left: 620px; }

  /* Front */
  .front-brand {
    position: absolute;
    left: 0; right: 0; top: 110px;
    display: flex; align-items: center; justify-content: center; gap: 14px;
  }
  .brand-mark {
    width: 34px; height: 34px;
    background: var(--red);
  }
  .brand-name {
    font-weight: 700;
    font-size: 30px;
    letter-spacing: 1px;
    text-transform: uppercase;
    color: var(--cyan);
  }
  .edge-stripe {
    position: absolute; left: 0; right: 0; bottom: 0; height: 8px;
    display: flex;
  }
  .edge-stripe__red { flex: 7; background: var(--red); }
  .edge-stripe__cyan { flex: 3; background: var(--cyan); margin-left: 4px; }

  /* Back */
  .back-info { position: absolute; left: 34px; top: 40px; }
  .back-info .brand-name { font-size: 22px; display: block; margin-bottom: 16px; }
  .person-name {
    font-weight: 700; font-size: 28px; color: var(--cyan);
    text-transform: uppercase; line-height: 1.05;
  }
  .person-role { font-size: 15px; color: var(--red); margin-bottom: 16px; }
  .contact-list { list-style: none; }
  .contact-item {
    display: flex; align-items: flex-start; gap: 10px;
    color: var(--text-light); font-size: 13px; line-height: 1.35;
    margin-bottom: 6px;
  }
  .contact-icon {
    flex: none; width: 16px; height: 16px; margin-top: 1px;
    background: var(--cyan); border-radius: 4px;
    display: flex; align-items: center; justify-content: center;
  }
  .contact-icon svg { width: 10px; height: 10px; fill: none; stroke: var(--card); stroke-width: 2; }
  .back-mark {
    position: absolute; right: 44px; top: 62px;
    width: 180px; height: 180px;
    background: var(--red);
  }
</style>
</head>
<body>

<section class="card card--front" aria-label="Card front">
  <div class="front-brand">
    <span class="brand-mark"></span>
    <span class="brand-name">Veldmark Supplies</span>
  </div>
  <div class="edge-stripe"><span class="edge-stripe__red"></span><span class="edge-stripe__cyan"></span></div>
</section>

<section class="card card--back" aria-label="Card back">
  <div class="back-info">
    <span class="brand-name">Veldmark Supplies</span>
    <h1 class="person-name">Daniel Ostrow</h1>
    <p class="person-role">Founder &amp; CEO</p>
    <ul class="contact-list">
      <li class="contact-item">
        <span class="contact-icon"><svg viewBox="0 0 10 10"><path d="M5 9 C2 5 2 4 2 3.5 A3 3 0 0 1 8 3.5 C8 4 8 5 5 9Z"/></svg></span>
        <span>423 Street Address Here, City<br>State &amp; Country, ZIP Code</span>
      </li>
      <li class="contact-item">
        <span class="contact-icon"><svg viewBox="0 0 10 10"><path d="M2 1.5 L4 1.5 L4.5 3.5 L3.5 4.5 C4 6 4.5 6.5 6 7 L7 6 L9 6.5 L9 8.5 C5 9 1.5 5.5 2 1.5Z"/></svg></span>
        <span>(123) 456-7890</span>
      </li>
      <li class="contact-item">
        <span class="contact-icon"><svg viewBox="0 0 10 10"><rect x="3" y="1" width="4" height="8" rx="1"/></svg></span>
        <span>(123) 456-7890</span>
      </li>
      <li class="contact-item">
        <span class="contact-icon"><svg viewBox="0 0 10 10"><rect x="1" y="2.5" width="8" height="5"/><path d="M1 2.5 L5 5.5 L9 2.5"/></svg></span>
        <span>info@yourwebsitehere.com</span>
      </li>
      <li class="contact-item">
        <span class="contact-icon"><svg viewBox="0 0 10 10"><circle cx="5" cy="5" r="3.8"/><path d="M1.2 5 H8.8 M5 1.2 C3 3.5 3 6.5 5 8.8 M5 1.2 C7 3.5 7 6.5 5 8.8"/></svg></span>
        <span>yourwebsitehere.com</span>
      </li>
    </ul>
  </div>
  <div class="back-mark" aria-hidden="true"></div>
</section>

</body>
</html>
```